Larkfield Ridge Management

I need a professional website. My current website is larkfieldridgemanagement.com and I hate it. It was created with some AI tool very quickly because I needed a site up and running with no advanced notice. I’m open to all designs .. I trust you, the professionals will deliver the results I’m anxiously awaiting! :)

```html
<!DOCTYPE html>
<html lang="en">
<head>
<meta charset="UTF-8">
<title>Larkfield Ridge Management LLC</title>
<link href="https://fonts.googleapis.com/css2?family=Poppins:wght@400;500;600;700;800&display=swap" rel="stylesheet">
<style>
:root{
  --navy:#1f3157;
  --red:#d0272e;
  --grey:#f2f2f2;
  --ink:#222;
  --footer:#1e1e1e;
  --white:#fff;
}
*{margin:0;padding:0;box-sizing:border-box}
html,body{width:1200px;height:2642px;overflow:hidden}
body{position:relative;font-family:'Poppins',sans-serif;color:var(--ink);background:var(--white)}

/* header */
.site-header{position:absolute;left:0;top:0;width:1200px;height:82px;background:var(--white);z-index:5}
.brand{position:absolute;left:75px;top:26px;display:flex;align-items:center;gap:10px;font-weight:800;font-size:20px;color:var(--navy);letter-spacing:.5px}
.brand-dot{width:26px;height:26px;border-radius:50%;background:var(--navy)}
.main-nav{position:absolute;top:34px;left:0;width:1200px;font-size:14.5px;font-weight:500}
.main-nav a{position:absolute;color:var(--ink);text-decoration:none;letter-spacing:.3px}
.main-nav a.active{color:var(--red);font-weight:600}

/* hero */
.hero-photo{position:absolute;left:0;top:82px;width:1200px;height:660px;
  background:linear-gradient(180deg,#4d7fc0 0%,#8fb0d8 28%,#c7d2d8 40%,#5e6f58 50%,#7d7466 65%,#8a5b4f 80%,#4e5548 100%)}
.hero-edge{position:absolute;left:0;top:640px;width:1200px;height:110px}
.hero-title{position:absolute;left:0;top:226px;width:1200px;text-align:center;color:var(--white);font-weight:800;font-size:76px;line-height:70px;letter-spacing:1px}
.hero-tagline{position:absolute;left:0;top:374px;width:1200px;text-align:center;color:var(--white);font-size:30px;font-weight:500;letter-spacing:.5px}
.btn{display:flex;align-items:center;justify-content:center;background:var(--red);color:var(--white);font-weight:700;font-size:15.5px;letter-spacing:.3px}
.hero-btn{position:absolute;left:530px;top:438px;width:140px;height:49px}

/* welcome */
.navy-band{position:absolute;left:0;top:1080px;width:1200px;height:744px;background:var(--navy)}
.welcome-card{position:absolute;left:75px;top:811px;width:1051px;height:452px}
.welcome-title{position:absolute;left:629px;top:848px;width:480px;font-weight:800;font-size:34px;line-height:41px;color:var(--navy);letter-spacing:.3px}
.welcome-sub{position:absolute;left:629px;top:939px;font-size:17.5px;font-weight:500;color:var(--red);letter-spacing:.4px}
.welcome-text{position:absolute;left:630px;top:971px;width:475px;font-size:15px;line-height:24px;color:var(--ink)}
.welcome-text p+p{margin-top:8px}
.welcome-btn{position:absolute;left:630px;top:1147px;width:141px;height:49px}

/* services */
.services-title{position:absolute;left:0;top:1327px;width:1200px;text-align:center;color:var(--white);font-weight:700;font-size:36px;letter-spacing:.5px}
.services-intro{position:absolute;left:150px;top:1391px;width:900px;text-align:center;color:var(--white);font-size:15.5px;line-height:25px}
.service{position:absolute;top:1459px;width:242px;text-align:center;color:var(--white)}
.service-photo{width:242px;height:153px}
.service h3{margin-top:21px;font-size:16px;font-weight:700;letter-spacing:.3px}
.service p{margin-top:10px;font-size:14px;line-height:22.5px}

/* proposal */
.proposal-bg{position:absolute;left:0;top:1824px;width:1200px;height:680px;
  background:linear-gradient(180deg,#fbfcfd 0%,#f3f5f7 35%,#d9dee0 60%,#b8b3a8 80%,#a8a89a 100%)}
.proposal-title{position:absolute;left:74px;top:1895px;font-weight:800;font-size:36px;line-height:44px;color:var(--navy);letter-spacing:.5px}
.proposal-text{position:absolute;left:75px;top:1992px;width:600px;font-size:15.5px;line-height:25px}
.field{position:absolute;background:var(--white);border:1px solid #d6d6d6;font-size:13.5px;color:var(--ink);padding:14px 16px}
.submit-btn{position:absolute;left:75px;top:2264px;width:139px;height:49px}
.proposal-brand{position:absolute;left:740px;top:2020px;width:390px;text-align:center;color:var(--navy);font-weight:800;font-size:46px;line-height:54px;letter-spacing:1px}
.proposal-brand .mark{width:60px;height:60px;border-radius:50%;background:var(--navy);margin:0 auto 20px}

/* footer */
.footer-edge{position:absolute;left:0;top:2400px;width:1200px;height:120px}
.site-footer{position:absolute;left:0;top:2500px;width:1200px;height:142px;background:var(--footer);color:var(--white)}
.footer-nav{position:absolute;left:75px;top:46px;font-size:15px;font-weight:600;display:flex;gap:37px}
.footer-mail{position:absolute;right:72px;top:46px;font-size:15px;font-weight:600}
.copyright{position:absolute;left:75px;top:85px;font-size:12.5px;color:#ddd}
.social{position:absolute;right:82px;top:86px;display:flex;gap:20px}
.social span{width:22px;height:22px;border-radius:50%;background:var(--white)}
.social span.accent{background:var(--red)}
</style>
</head>
<body>

<header class="site-header">
  <div class="brand"><span class="brand-dot"></span>LARKFIELD RIDGE</div>
  <nav class="main-nav">
    <a class="active" style="left:756px">HOME</a>
    <a style="left:845px">SERVICES</a>
    <a style="left:960px">ABOUT</a>
    <a style="left:1055px">CONTACT</a>
  </nav>
</header>

<section class="hero">
  <div class="hero-photo" role="img" aria-label="Aerial view of a suburban neighbourhood under a blue sky with clouds"></div>
  <svg class="hero-edge" viewBox="0 0 1200 110" preserveAspectRatio="none">
    <polygon points="0,0 602,74 1200,0 1200,110 0,110" fill="#fff"/>
    <polygon points="0,20 602,92 1200,20 1200,28 602,98 0,28" fill="#1f3157"/>
  </svg>
  <h1 class="hero-title">LARKFIELD RIDGE<br>MANAGEMENT LLC</h1>
  <p class="hero-tagline">A true partner, not just a vendor.</p>
  <a class="btn hero-btn">READ MORE</a>
</section>

<div class="navy-band"></div>

<section class="welcome">
  <svg class="welcome-card" viewBox="0 0 1051 452">
    <defs>
      <linearGradient id="handshake" x1="0" y1="0" x2="1" y2="1">
        <stop offset="0" stop-color="#2b3f78"/>
        <stop offset=".45" stop-color="#c9b7a4"/>
        <stop offset="1" stop-color="#eceae6"/>
      </linearGradient>
    </defs>
    <polygon points="0,0 525,0 525,452 0,362" fill="url(#handshake)" role="img" aria-label="Business handshake above two small model houses"/>
    <polygon points="525,0 1051,0 1051,362 525,452" fill="#f2f2f2"/>
  </svg>
  <h2 class="welcome-title">WELCOME  LARKFIELD RIDGE MANAGEMENT LLC</h2>
  <p class="welcome-sub">EXPERTISE ROOTED IN ASSET PRESERVATION</p>
  <div class="welcome-text">
    <p>The organization applies rigorously tested frameworks and data-driven methodologies to safeguard property value while elevating tenant experience.</p>
    <p>Our organization delivers comprehensive property management solutions that optimize asset performance and tenant satisfaction.</p>
  </div>
  <a class="btn welcome-btn">READ MORE</a>
</section>

<section class="services">
  <h2 class="services-title">OUR SERVICES</h2>
  <p class="services-intro">Our analysis demonstrates that effective property oversight originates from meticulous operational planning, transparent communication channels, and data-driven performance metrics across every asset class.</p>

  <div class="service" style="left:75px">
    <div class="service-photo" role="img" aria-label="Hands reviewing documents beside an architectural house model" style="background:linear-gradient(135deg,#4a3a34 0%,#c9b9a3 55%,#e6ddd0 100%)"></div>
    <h3>RESIDENTIAL MANAGEMENT</h3>
    <p>Professional day-to-day management that protects your investment while delivering an exceptional resident experience.</p>
  </div>
  <div class="service" style="left:345px">
    <div class="service-photo" role="img" aria-label="Pen signing papers next to wooden house models and a piggy bank" style="background:linear-gradient(135deg,#5c5650 0%,#c8a27a 55%,#e2d6c6 100%)"></div>
    <h3>LEASING SERVICES</h3>
    <p>From marketing to lease signing, we help fill vacancies with qualified tenants quickly.</p>
  </div>
  <div class="service" style="left:615px">
    <div class="service-photo" role="img" aria-label="Maintenance worker with a clipboard in front of an apartment building" style="background:linear-gradient(135deg,#2b3450 0%,#7a8aa0 50%,#e0c79c 100%)"></div>
    <h3>MAINTENANCE &amp; REPAIRS</h3>
    <p>Reliable maintenance programs and trusted vendor networks keep your property operating at its best.</p>
  </div>
  <div class="service" style="left:885px">
    <div class="service-photo" role="img" aria-label="People reviewing financial charts on paper and a tablet" style="background:linear-gradient(135deg,#e4e6e8 0%,#b8c2cc 55%,#3e3a38 100%)"></div>
    <h3>FINANCIAL REPORTING</h3>
    <p>Transparent reporting, rent collection, and owner statements provide complete visibility into your investment.</p>
  </div>
</section>

<section class="proposal">
  <div class="proposal-bg" role="img" aria-label="Faded aerial view of a new housing development"></div>
  <h2 class="proposal-title">REQUEST A TAILORED<br>PROPOSAL</h2>
  <p class="proposal-text">Submit the form to initiate a consultative assessment and explore solutions aligned with your objectives.</p>
  <div class="field" style="left:75px;top:2066px;width:290px;height:49px">Full Name</div>
  <div class="field" style="left:385px;top:2066px;width:290px;height:49px">Email Addres</div>
  <div class="field" style="left:75px;top:2126px;width:600px;height:127px">Message</div>
  <a class="btn submit-btn">SUBMIT</a>
  <div class="proposal-brand"><div class="mark"></div>LARKFIELD RIDGE<br>MANAGEMENT</div>
</section>

<svg class="footer-edge" viewBox="0 0 1200 120" preserveAspectRatio="none">
  <polygon points="0,78 602,30 1200,78 1200,120 0,120" fill="#fff"/>
  <polygon points="0,84 602,38 1200,84 1200,100 0,100" fill="#1f3157"/>
  <polygon points="0,100 602,52 1200,100 1200,120 0,120" fill="#1e1e1e"/>
</svg>

<footer class="site-footer">
  <nav class="footer-nav"><span>Home</span><span>Services</span><span>About Us</span><span>Contact Us</span></nav>
  <div class="footer-mail">info@larkfieldridgemanagement.com</div>
  <p class="copyright">© 2026. Company Name. All Right Reserved</p>
  <div class="social"><span></span><span class="accent"></span><span></span><span></span><span></span></div>
</footer>

</body>
</html>
```